Blogging Platform for Christian Missions

We need the main (one) page design for FaithTrailer. FaithTrailer is a blogging platform for people (missionaries) who work for Christian Mission organisations in various countries. It will provides an easy way for them to setup and maintain a blog that will have features specifically for missions.

There's a lot of work involved in creating a web page design so I am happy to receive many quick rough designs. I will select my favourite four or five designs and these can submit the full design.

Please see the attached wireframe. Please also see the attached logo.

Main colours
- black
- white
- grey
- red (see logo colour) can be used occasionally eg. titles
- another complementary colour - occasionally used

Photos uploaded by the missionaries will provide colour for the website.

It needs to be a clean design that is not cluttered. The main focus are the blog posts. The information on the side complements the blog. There are navigational options at the top and bottom. The FaithTrailer logo is not the main focus. The person's name (blog owner) is what needs to be most prominent.

I love the BrightKarnu design (http://www.brightkarnu.com/). I particularly like the soft design - light grey background, white background boxes for content. The focus is the content - text and photos. I also like the subtle use of breakout image - "Step into the Venture". I like the black navigation header and the black footer. I do not want a exact copy of the site but I'd like to use this concept .

I also like this Vexlo design (http://calm.vexlo.com/theme/preview/5194) because of the white box (and the shadow) for the content. I also like how the word "Quote" and the number of "notes" breaks out of the white content area (see attachment). I'd like to do this, if possible with the date. This is just a "nice to have" - definitely not essential. I don't like the font for the title in this example.

We have build a simple prototype already. I cautiously show this because I want the the design of this to be completely ignored. I used a free template. Along with the wireframe this prototype should an idea of what kind of content will be displayed but please don't look too much at it.
http://faithtrailer.org/blog/1

The design will be used to create a website using Plonkit. We will use zScriptor so feel free to suggest an animation or lightbox effect to make your design more dynamic. This is a nice to have.

Once we have our final design we will need to define the style for:
- h1 through h4 tags
- Paragraphs
- Lists
- Block quotes
- Italics, bolding and underlining
- Links, including active, hover and visited states

Please let me know what additional information you need. Also let me know if there is something I have not considered.

Target Market(s)

The target customers are mission workers aged 25-35 who will post blog entries. These posts will be read by their friends and family.

Industry/Entity Type

Build

Requirements
Must have
• Clean simple design. Must be inspired by the BrightKarnu (http://www.brightkarnu.com/) design without copying it.
Nice to have
• Design element that breaks out of the boxes. See the screenshot attached from the Vexlo site. Described more in the project overview.
Should not have
• Should not use fonts that are not web-friendly. Should not have features that will be difficult to implement using HTML/CSS.

```html
<!DOCTYPE html>
<html lang="en">
<head>
<meta charset="utf-8">
<title>Hannah Reed – FaithTrailer</title>
<link href="https://fonts.googleapis.com/css2?family=Arimo:ital,wght@0,400;0,700;1,400&family=Libre+Baskerville:ital@1&display=swap" rel="stylesheet">
<style>
:root{
  --red:#e2001a;
  --nav:#3b3b3b;
  --footer:#262626;
  --page:#ebebeb;
  --side:#f1f1f1;
  --rule:#dcdcdc;
  --ink:#333;
  --muted:#999;
  --head:#555;
}
*{box-sizing:border-box;margin:0;padding:0}
html,body{width:930px;height:1200px;overflow:hidden}
body{font-family:"Arimo",Arial,sans-serif;color:var(--ink);background:var(--page);position:relative}
a{color:inherit;text-decoration:none}

.topnav{height:28px;background:var(--nav);display:flex;justify-content:space-between;align-items:center;padding:0 50px;font-size:11px;font-weight:700;text-transform:uppercase;color:#fff}
.topnav ul{display:flex;list-style:none;height:28px;align-items:center}
.topnav li{padding:0 11px;line-height:28px}
.topnav li.active{background:var(--red);padding:0 12px}
.topnav .account li{padding:0 8px}
.topnav .sep{color:#999;padding:0}

.masthead{height:108px;background:#fff;position:relative;border-bottom:1px solid #e3e3e3}
.brand{position:absolute;left:55px;top:32px;display:flex;align-items:center;gap:12px;font-size:38px;color:#444}
.brand .dot{width:40px;height:40px;border-radius:50%;background:var(--red)}
.search{position:absolute;left:658px;top:76px;width:215px;height:24px;border:1px solid #e6e6e6;background:#fafafa}
.search svg{position:absolute;right:8px;top:4px}

.main{position:absolute;left:0;top:136px;width:633px;height:929px}
.owner{position:absolute;left:58px;top:32px}
.owner h1{font-size:29px;font-weight:400;color:#4a4a4a}
.owner p{font-size:16px;color:#777;margin-top:4px}

.post{position:absolute;left:42px;width:571px;background:#fff;box-shadow:0 1px 5px rgba(0,0,0,.18);padding:12px 18px}
.post h2{font-size:22px;font-weight:400;color:var(--red)}
.post .meta{font-size:10px;color:var(--muted);margin:6px 0 12px}
.post p{font-size:10.5px;line-height:19px;color:#444;margin-bottom:12px}
.share{position:absolute;right:16px;top:12px;display:flex;gap:6px}
.share span{width:22px;height:22px;border-radius:3px;background:#3b5998}
.share span+span{background:#3cb4e0}
.photo{height:229px;background:linear-gradient(180deg,#c8a06a 0%,#a4553d 55%,#7a2a24 80%,#3d2b22 100%);margin:4px 0 14px}
.post-foot{height:22px;background:#efefef;display:flex;justify-content:space-between;align-items:center;padding:0 14px;font-family:"Libre Baskerville",Georgia,serif;font-style:italic;font-size:10px;color:#888}
.post-foot .bubble{display:inline-block;width:10px;height:8px;background:var(--red);border-radius:2px;margin-right:9px;vertical-align:middle}
.post-foot .more{color:var(--red)}

.pager{position:absolute;top:887px;left:150px;display:flex;gap:8px}
.pager a{height:26px;min-width:32px;padding:0 12px;border:1px solid #ddd;background:#fff;font-size:11px;color:#aaa;display:flex;align-items:center;justify-content:center}
.pager a.current{background:var(--red);color:#fff;border-color:var(--red);font-weight:700}
.pager a.wide{width:60px}

.sidebar{position:absolute;left:633px;top:136px;width:255px;height:929px;background:var(--side);border-left:1px solid #dedede;border-right:1px solid #dedede}
.widget{padding:10px 10px 0 12px;border-bottom:1px solid var(--rule)}
.widget h3{font-size:15px;font-weight:400;color:#777;margin-bottom:10px}
.widget p{font-size:10px;line-height:15px;color:#444}
.widget .link{display:block;font-size:10px;color:#aaa;text-decoration:underline;margin:8px 0 6px}
.follow a{display:flex;align-items:center;width:206px;height:34px;margin:0 0 8px 16px;background:#fff;border:1px solid #ddd;border-radius:3px;padding:0 6px;font-size:14px;color:#2a4f7a}
.follow a .sq{width:24px;height:24px;border-radius:3px;background:#3b5998;margin-right:10px}
.follow a.chirp .sq{background:#3cb4e0}
.follow a em{margin-left:auto;font-family:"Libre Baskerville",Georgia,serif;color:#bbb;font-size:15px;border-left:1px solid #ddd;padding-left:12px}
.about{display:flex;gap:8px}
.avatar{flex:0 0 102px;height:80px;background:#505050;border:3px solid #ccc}
.map{height:100px;margin:0 10px 8px;background:linear-gradient(135deg,#e6e2d4,#f1edd9 60%,#e3dfc9);border:3px solid #ccc}
.events li{list-style:none;font-size:10px;line-height:15px;color:#444}
.events.bullets li::before{content:"•";color:#777;margin-right:6px}

.footer{position:absolute;left:0;top:1065px;width:930px;height:135px;background:var(--footer);color:#fff;padding:16px 58px}
.cols{display:flex}
.cols div{font-size:10px;line-height:14px}
.cols div:nth-child(1){width:147px}
.cols div:nth-child(2){width:172px}
.cols h4{font-size:11px;margin-bottom:10px}
.footer .brand{left:645px;top:50px;font-size:26px;color:#fff;gap:8px}
.footer .brand .dot{width:28px;height:28px;background:#fff}
</style>
</head>
<body>
<nav class="topnav">
  <ul class="primary">
    <li class="active">Mission Blogs</li><li>Opportunities</li><li>Option3</li><li>Option4</li>
  </ul>
  <ul class="account"><li>Sign In</li><li class="sep">|</li><li>Register</li></ul>
</nav>

<header class="masthead">
  <div class="brand"><span class="dot"></span>faithtrailer.org</div>
  <div class="search">
    <svg width="14" height="14" viewBox="0 0 14 14"><circle cx="6" cy="6" r="4" fill="none" stroke="#888" stroke-width="1.6"/><line x1="9" y1="9" x2="13" y2="13" stroke="#888" stroke-width="1.8"/></svg>
  </div>
</header>

<main class="main">
  <div class="owner"><h1>Hannah Reed</h1><p>Wayfarer Australia</p></div>

  <article class="post" style="top:120px;height:504px">
    <h2>Just Arrived</h2>
    <div class="share"><span></span><span></span></div>
    <div class="meta">Submitted by Hannah Reed on Mon, 14 April 2011 - 07:58</div>
    <p>Lorem ipsum dolor sit amet, consectetuer adipiscing elit. Aenean commodo ligula eget dolor. Aenean massa. Cum sociis natoque penatibus et magnis dis parturient montes, nascetur ridiculus mus. Donec quam felis, ultricies nec, pellentesque eu, pretium quis, sem. Nulla consequat massa quis enim. , justo. Nullam dictum felis eu pede mollis pretium. Integer tincidunt. Cras dapibus.</p>
    <p>Enim. Aliquam lorem ante, dapibus in, viverra quis, feugiat a, tellus. Phasellus viverra nulla ut metus varius laoreet. Quisque rutrum. Aenean imperdiet. Etiam ultricies nisi vel augue. Curabitur ullamcorper ultricies nisi. Nam eget dui. Etiam rhoncus. Maecenas tempus, tellus eget condimentum</p>
    <div class="photo" role="img" aria-label="Photo of a living room with red sofas and a dark coffee table"></div>
    <div class="post-foot"><span><span class="bubble"></span>4 comments</span><a class="more" href="#">Read more</a></div>
  </article>

  <article class="post" style="top:647px;height:226px">
    <h2>Only 14 days to go before I fly for Malawi</h2>
    <div class="share"><span></span><span></span></div>
    <div class="meta">Submitted by Hannah Reed on Mon, 30 March 2011 - 09:00</div>
    <p>Lorem ipsum dolor sit amet, consectetuer adipiscing elit. Aenean commodo ligula eget dolor. Aenean massa. Cum sociis natoque penatibus et magnis dis parturient montes, nascetur ridiculus mus. Donec quam felis, ultricies nec, pellentesque eu, pretium quis, sem. Nulla consequat massa quis enim.Enim. Aliquam lorem ante, dapibus in, viverra quis, feugiat a, tellus. Phasellus viverra nulla ut metus varius laoreet. Quisque rutrum. Aenean imperdiet. Etiam ultricies nisi vel augue. Curabitur ullamcorper ultricies nisi. Nam eget dui. Etiam rhoncus. Maecenas tempus, tellus eget condimentum</p>
    <div class="post-foot"><span><span class="bubble"></span>4 comments</span><a class="more" href="#">Read more</a></div>
  </article>

  <div class="pager">
    <a class="wide">Previous</a><a class="current">1</a><a>2</a><a>3</a><a>4</a><a>5</a><a class="wide">Next</a>
  </div>
</main>

<aside class="sidebar">
  <section class="widget follow" style="height:141px">
    <h3>Follow Hannah Reed</h3>
    <a href="#"><span class="sq"></span>Find us on Linkwall<em>134</em></a>
    <a href="#" class="chirp"><span class="sq"></span>Follow us on Chirper<em>134</em></a>
  </section>
  <section class="widget" style="height:153px">
    <h3>About Hannah</h3>
    <div class="about"><div class="avatar" role="img" aria-label="Profile photo of Hannah Reed"></div>
    <p>Lorem ipsum dolor sit amet, consectetuer adipiscing elit. Aenean commodo ligula eget dolor. Aenean</p></div>
    <a class="link" href="#">View my complete profile</a>
  </section>
  <section class="widget" style="height:159px">
    <h3>About Hannah's Ministry</h3>
    <p>Lorem ipsum dolor sit amet, consectetuer adipiscing elit. Aenean commodo ligula eget dolor. Aenean Lorem ipsum dolor sit amet, consectetuer adipiscing elit. Aenean commodo ligula eget dolor. Aenea Lorem ipsum</p>
    <a class="link" href="#">Read more</a>
  </section>
  <section class="widget" style="height:229px">
    <h3>About Malawi</h3>
    <div class="map" role="img" aria-label="Street map with a location pin"></div>
    <p>Lorem ipsum dolor sit amet, consectetuer adipiscing elit. Aenean commodo ligula eget dolor. Aenean Lorem</p>
    <a class="link" href="#">Read more</a>
  </section>
  <section class="widget" style="height:97px">
    <h3>Wayfarer Events</h3>
    <ul class="events"><li>Wayfarer Prayer Event - May 15th</li><li>Wayfarer Conference - June 30th</li></ul>
  </section>
  <section class="widget" style="height:125px;border:0">
    <h3>Wayfarer Events</h3>
    <ul class="events bullets"><li>Teacher in Blanta (2yrs)</li><li>Financial Controller (long term)</li><li>Project Manager (6months+)</li><li>Bible College Lecturer (long term)</li></ul>
    <a class="link" href="#">Read more</a>
  </section>
</aside>

<footer class="footer">
  <div class="cols">
    <div><h4>About Us</h4>About FaithTrailer<br>Missionaries<br>Mission Agencies<br>Churches<br>Mission Supporters<br>Privacy</div>
    <div><h4>Regions Mission</h4>Africa<br>Asia<br>North America<br>Latin America<br>Aust/Pacific</div>
    <div><h4>Agencies</h4>CTS<br>Harbour Outreach<br>Wayfarer Australia<br>NRC</div>
  </div>
  <div class="brand"><span class="dot"></span>faithtrailer.org</div>
</footer>
</body>
</html>
```